Vantor Apparel - T-Shirts on Storevia

Hi - I'm creating a new site to sell undershirts. The premise of the undershirt is that it has a U-neck shape so that your white undershirt does not show when you are wearing a button shirt. I want the site to be fun but still look stunning because I want to attract a certain clientele (business professionals with a sense of humor). I'm creating a funny video to post on the site to hopefully get some social media buzz.
I want the design to highlight the product but more importantly the lifestyle of the person who wears it. This is an undershirt so nobody really sees it and that's the point.
Since this is a single product that I want to sell, I want to make sure that the design works with Storevia. Since this is not for theme development, this design must work with an existing theme on Storevia (preferably free but if you must then no more than $75). You can choose the theme to design for.
Products:
* Single vantor undershirt in 4 sizes - S, M, L and XL
* 3 packs or 7 packs (buy 6 get 1 free)
* One-time purchase or subscription (delivery every 3 or 6 months) - I know this will require custom theme development
Attached you will find a very rough idea for the site and this was made before I had considered putting in a video (Brix template). It's going to be tough to catch lightning in a bottle much like Penny Razor Guild but that's what I'm hoping for.
Name of the company is Vantor Apparel. Logo attached. Included .ai file which has some funky colors so please use the light blue color logo similar to the png's attached.
Here is the site for a competitor. There's much to be improved on the site but I include it here because the concept of the undershirt is the same: http://www.mirelgarments.example
Feel free to use stock images that I can purchase on the site that represents a young and cool vibe. I will be taking shots of the shirts for the product page so for now use some generic shirt please.
Updates
Project Deadline Extended
Reason: Please take a look at feedback for other designs. I'm hoping for my mockup to be an inspiration, not just re-skinning the mockup I created. Plus it must be based on a Storevia theme. Use stock images as necessary but keep the budget for purchasing images under $100.
Target Market(s)
Male 30-50

```html
<!DOCTYPE html>
<html lang="en">
<head>
<meta charset="utf-8">
<title>Vantor Apparel</title>
<link rel="stylesheet" href="https://fonts.googleapis.com/css2?family=Oswald:wght@400;500;700&family=Open+Sans:wght@400;600;700&display=swap">
<style>
:root{
  --ink:#1c1c1c;
  --topbar:#1e1e1e;
  --blue:#2a9fd8;
  --blue-dark:#1d86bb;
  --blue-light:#45b3e6;
  --dark:#2d2927;
  --dark-panel:#3a3533;
  --footer:#1f1b1a;
  --grey-text:#777;
  --light-box:#f2f2f2;
  --white:#fff;
}
*{margin:0;padding:0;box-sizing:border-box}
html,body{width:1200px;height:3214px;overflow:hidden}
body{position:relative;background:var(--white);font-family:"Open Sans",Arial,sans-serif;color:var(--ink)}
.abs{position:absolute}
.heading{font-family:"Oswald","Arial Narrow",sans-serif;font-weight:700;text-transform:uppercase;letter-spacing:1px}

.topbar{left:0;top:0;width:1200px;height:54px;background:var(--topbar);color:#ddd;font-size:12px}
.topbar .welcome{left:94px;top:19px}
.topbar .links{right:96px;top:19px;display:flex;gap:34px}

.header{left:0;top:54px;width:1200px;height:112px}
.logo{left:120px;top:32px;font-size:34px;font-weight:700;color:var(--ink);letter-spacing:-.5px}
.nav{right:96px;top:47px;display:flex;gap:32px;align-items:center;font-family:"Oswald",sans-serif;font-weight:500;font-size:15px;text-transform:uppercase}

.hero{left:0;top:166px;width:1200px;height:442px;overflow:hidden;
  background:
    radial-gradient(ellipse 190px 230px at 360px 230px,rgba(236,196,150,.85),rgba(236,196,150,0) 70%),
    radial-gradient(ellipse 240px 260px at 260px 360px,rgba(232,172,190,.9),rgba(232,172,190,0) 70%),
    radial-gradient(ellipse 200px 250px at 470px 380px,rgba(214,190,200,.8),rgba(214,190,200,0) 70%),
    linear-gradient(90deg,#2e2e2e 0%,#4d4d4d 9%,#7a7775 15%,#e6e2de 30%,#f3f1ee 52%,#eceef0 64%,#aebdc8 80%,#93a6b4 100%)}
.hero-line{position:absolute;background:#000;color:#fff;text-align:center;font-family:"Oswald",sans-serif;font-weight:700;text-transform:uppercase;white-space:nowrap}
.hero-1{left:718px;top:123px;width:300px;height:54px;font-size:28px;line-height:54px;letter-spacing:1.5px}
.hero-2{left:656px;top:185px;width:432px;height:75px;font-size:58px;line-height:71px;border:2px solid #fff;letter-spacing:1px}
.hero-3{left:769px;top:271px;width:169px;height:48px;font-size:27px;line-height:48px;letter-spacing:2px}

.title-box{border:2px solid var(--ink);text-align:center;font-size:21px;line-height:50px}
.title-box.light{border-color:#fff;color:#fff}
.new-title{left:453px;top:678px;width:295px;height:54px}
.intro{left:150px;top:780px;width:900px;text-align:center;font-size:11.5px;line-height:20px;color:var(--grey-text)}
.read-more{font-family:"Oswald",sans-serif;font-weight:700;font-size:12px;text-transform:uppercase;letter-spacing:.5px}
.intro-more{left:560px;top:848px;width:80px;text-align:center}

.product{width:320px;top:898px}
.product .shot{width:260px;height:282px;margin:0 auto;
  background:radial-gradient(ellipse 120px 110px at 50% 48%,#fafafa 0%,#ececec 55%,rgba(255,255,255,0) 100%),
             radial-gradient(ellipse 130px 125px at 55% 62%,#e4e4e4 0%,rgba(255,255,255,0) 100%),#fff}
.product .name{margin-top:28px;text-align:center;font-size:15px;line-height:19px}
.price-btn{display:flex;width:209px;height:38px;margin:24px auto 0;color:#fff;font-family:"Oswald",sans-serif;font-weight:700;font-size:13px;text-transform:uppercase;letter-spacing:.5px}
.price-btn+.price-btn{margin-top:13px}
.price-btn .label{flex:1;background:var(--blue);line-height:38px;padding-left:14px}
.price-btn .amount{width:64px;background:var(--blue-dark);line-height:38px;text-align:center}

.shop-now{left:482px;top:1423px}

.blog{left:0;top:1543px;width:1200px;height:762px;background:var(--dark)}
.blog-title{left:429px;top:73px;width:340px;height:51px;font-size:21px}
.post{width:300px;color:#fff}
.post .num{position:absolute;left:0;top:0;width:45px;height:45px;background:var(--blue);font-family:"Oswald",sans-serif;font-weight:700;font-size:28px;line-height:45px;text-align:center}
.post .ptitle{position:absolute;left:66px;top:6px;font-size:19px;white-space:nowrap}
.post .rule{position:absolute;left:66px;top:38px;width:40px;height:2px;background:#fff}
.post .text{position:absolute;left:0;top:60px;width:300px;font-size:11.5px;line-height:18px;color:#cfcfcf}
.post .read-more{position:absolute;left:0;top:136px;color:#fff}

.promo{left:94px;top:620px;width:1010px;height:123px}
.promo-photo{left:0;top:0;width:415px;height:123px;
  background:radial-gradient(ellipse 60px 70px at 65px 70px,#f4f4f4 0%,#dcdcdc 50%,rgba(200,200,200,0) 100%),
             linear-gradient(90deg,#6a6a6a,#8d8d8d 40%,#7a7a7a 70%,#5e5e5e)}
.promo-photo-text{left:160px;top:38px;color:#fff;font-size:20px;line-height:24px}
.promo-btn{border:2px solid #fff;color:#fff;font-family:"Oswald",sans-serif;font-weight:700;font-size:13px;text-transform:uppercase;text-align:center;height:42px;line-height:38px;width:102px}
.promo-blue{left:415px;top:0;width:595px;height:123px;background:var(--blue)}
.promo-blue-text{left:28px;top:38px;color:#fff;font-size:22px;line-height:23px;white-space:nowrap}
.promo-blue-text small{font-size:17px;display:block}

.says-title{left:220px;top:2357px;width:257px;height:51px;font-size:20px;line-height:47px}
.hl-title{left:710px;top:2357px;width:287px;height:51px;font-size:20px;line-height:47px}
.quote{left:96px;top:2473px;width:504px;height:219px;background:var(--light-box)}
.quote .who{position:absolute;left:20px;top:36px;font-size:17px;font-weight:500}
.quote .rule{position:absolute;left:20px;top:66px;width:40px;height:2px;background:var(--ink)}
.quote .text{position:absolute;left:20px;top:82px;width:460px;font-size:12px;line-height:20px;color:var(--grey-text)}
.arrow-btn{position:absolute;top:170px;width:43px;height:41px;background:var(--blue)}
.video{left:678px;top:2473px;width:345px;height:219px;
  background:radial-gradient(ellipse 110px 95px at 200px 150px,#9db3d6 0%,rgba(157,179,214,.6) 55%,rgba(157,179,214,0) 100%),
             radial-gradient(ellipse 40px 45px at 195px 55px,#6b5a4c 0%,rgba(107,90,76,0) 100%),
             linear-gradient(110deg,#8e8e8e 0%,#c8c8c8 30%,#dedede 55%,#b9b9b9 100%)}
.play{left:145px;top:84px}

.features{left:0;top:2763px;width:1200px;height:358px;background:var(--dark)}
.feature{top:0;width:337px;height:340px;background:var(--dark-panel)}
.feature .bar{height:96px;background:var(--blue);display:flex;align-items:center;justify-content:center;gap:20px;color:#fff;font-size:20px}
.feature.mid .bar{background:var(--blue-light)}
.feature .rule{width:40px;height:2px;background:#fff;margin:30px auto 0}
.feature .text{width:280px;margin:22px auto 0;text-align:center;color:#d8d8d8;font-size:11.5px;line-height:19px}
.cards{display:flex;gap:10px;justify-content:center;margin-top:14px}
.cards span{width:46px;height:26px;background:#f4f4f4;border-radius:2px}
.feature .btn{position:absolute;left:50%;bottom:20px;transform:translateX(-50%);width:134px;height:37px;border:2px solid #fff;color:#fff;text-align:center;line-height:33px}

.footer{left:0;top:3121px;width:1200px;height:93px;background:var(--footer);color:#cfcfcf;font-size:12px}
.footer .copy{left:94px;top:38px}
.footer .fnav{left:415px;top:38px;display:flex;gap:22px;text-transform:uppercase}
.social{right:96px;top:32px;display:flex;gap:10px}
.social span{width:26px;height:26px;border-radius:2px}
</style>
</head>
<body>

<div class="abs topbar">
  <div class="abs welcome">Welcome to our online store! Login or Signup</div>
  <div class="abs links"><span>⚙ Setting</span><span>👤 My Account</span><span>🛒 Cart: 0 item</span></div>
</div>

<header class="abs header">
  <div class="abs logo">Vantor Apparel</div>
  <nav class="abs nav">
    <span>Home</span><span>Categories</span><span>About us</span><span>FAQs</span><span>Contact us</span>
    <svg width="16" height="16" viewBox="0 0 16 16"><circle cx="6.5" cy="6.5" r="5" fill="none" stroke="#1c1c1c" stroke-width="2"/><line x1="10.5" y1="10.5" x2="15" y2="15" stroke="#1c1c1c" stroke-width="2"/></svg>
  </nav>
</header>

<section class="abs hero" role="img" aria-label="Lifestyle photo of a smiling couple, a man in a pink shirt with a woman in a floral dress, by a window">
  <div class="hero-line hero-1">Undershirts for the</div>
  <div class="hero-line hero-2">Modern Man</div>
  <div class="hero-line hero-3">Buy Now</div>
</section>

<div class="abs title-box heading new-title">Our New Products</div>
<p class="abs intro">Lorem ipsum dolor sit amet rem eos illo omnis aut aperiam ab ipsam ipse odit aut aperiam aut aspernatur ventatis unde sed enim accusantium laudantium sunt perspiciatis ipsam sed doloremque ipsam dolores totam unde aut illo aut veritatis explicabo data quo dicta ventatis dicta sunt quasi eaque rem</p>
<div class="abs read-more intro-more">Read More</div>

<div class="abs product" style="left:121px">
  <div class="shot" role="img" aria-label="Two folded white undershirts"></div>
  <div class="name heading">Vantor Undershirt<br>3 Pack of Shirts</div>
  <div class="price-btn"><span class="label">Buy Now</span><span class="amount">$15</span></div>
  <div class="price-btn"><span class="label">Every 6 Month</span><span class="amount">$14</span></div>
</div>
<div class="abs product" style="left:440px">
  <div class="shot" role="img" aria-label="Three stacked white undershirts"></div>
  <div class="name heading">Vantor Undershirt<br>Buy 6 Get 1 Free/7 Shirts</div>
  <div class="price-btn"><span class="label">Buy Now</span><span class="amount">$78</span></div>
  <div class="price-btn"><span class="label">Every 6 Month</span><span class="amount">$72</span></div>
</div>
<div class="abs product" style="left:759px">
  <div class="shot" role="img" aria-label="Two folded white undershirts"></div>
  <div class="name heading">Vantor Undershirt<br>3 Pack of Shirts</div>
  <div class="price-btn"><span class="label">Buy Now</span><span class="amount">$15</span></div>
  <div class="price-btn"><span class="label">Every 6 Month</span><span class="amount">$14</span></div>
</div>

<svg class="abs shop-now" width="236" height="48" viewBox="0 0 236 48">
  <polygon points="0,0 236,0 218,48 18,48" fill="#2a9fd8"/>
  <text x="118" y="32" text-anchor="middle" fill="#fff" font-family="Oswald, sans-serif" font-weight="700" font-size="22" letter-spacing="1">SHOP NOW</text>
</svg>

<section class="abs blog">
  <div class="abs title-box light heading blog-title">Lates News From Blog</div>

  <article class="abs post" style="left:94px;top:190px"><div class="num">1</div><div class="ptitle heading">Amet Voluptatem</div><div class="rule"></div><p class="text">Lorem ipsum dolor sit amet rem eos illo omnis aperiam ab ipsam ipsa odit aut aperiam aspernatur ventatis unde enim accusantium laudantium laudantium sunt</p><div class="read-more">Read More</div></article>
  <article class="abs post" style="left:450px;top:190px"><div class="num">2</div><div class="ptitle heading">Amet Voluptatem</div><div class="rule"></div><p class="text">Lorem ipsum dolor sit amet rem eos illo omnis aperiam ab ipsam ipsa odit aut aperiam aspernatur ventatis unde enim accusantium laudantium laudantium sunt</p><div class="read-more">Read More</div></article>
  <article class="abs post" style="left:806px;top:190px"><div class="num">3</div><div class="ptitle heading">Amet Voluptatem</div><div class="rule"></div><p class="text">Lorem ipsum dolor sit amet rem eos illo omnis aperiam ab ipsam ipsa odit aut aperiam aspernatur ventatis unde enim accusantium laudantium laudantium sunt</p><div class="read-more">Read More</div></article>
  <article class="abs post" style="left:94px;top:399px"><div class="num">4</div><div class="ptitle heading">Amet Voluptatem</div><div class="rule"></div><p class="text">Lorem ipsum dolor sit amet rem eos illo omnis aperiam ab ipsam ipsa odit aut aperiam aspernatur ventatis unde enim accusantium laudantium laudantium sunt</p><div class="read-more">Read More</div></article>
  <article class="abs post" style="left:450px;top:399px"><div class="num">5</div><div class="ptitle heading">Amet Voluptatem</div><div class="rule"></div><p class="text">Lorem ipsum dolor sit amet rem eos illo omnis aperiam ab ipsam ipsa odit aut aperiam aspernatur ventatis unde enim accusantium laudantium laudantium sunt</p><div class="read-more">Read More</div></article>
  <article class="abs post" style="left:806px;top:399px"><div class="num">6</div><div class="ptitle heading">Amet Voluptatem</div><div class="rule"></div><p class="text">Lorem ipsum dolor sit amet rem eos illo omnis aperiam ab ipsam ipsa odit aut aperiam aspernatur ventatis unde enim accusantium laudantium laudantium sunt</p><div class="read-more">Read More</div></article>

  <div class="abs promo">
    <div class="abs promo-photo" role="img" aria-label="Man wearing a white undershirt against a concrete wall"></div>
    <div class="abs heading promo-photo-text">Buy 6 Get 1<br>Free</div>
    <div class="abs promo-btn" style="left:288px;top:40px">Shop Now</div>
    <div class="abs promo-blue">
      <div class="abs heading promo-blue-text">One - Time Purchase or Subscription<small>Delivery every 3 or 6 months</small></div>
      <div class="abs promo-btn" style="left:460px;top:40px">Shop Now</div>
    </div>
  </div>
</section>

<div class="abs title-box heading says-title">What They Says</div>
<div class="abs title-box heading hl-title">Highlights Product</div>

<div class="abs quote">
  <div class="who heading">John Doe, 25 yo</div>
  <div class="rule"></div>
  <p class="text">Lorem ipsum dolor sit amet rem eos illo omnis aperiam ab ipsam ipsa odit aut aperiam aut aspernatur ventatis unde sed enim accusan tium laudantium laudantium sunt perspiciatis ipsam sed doloremque . . .</p>
  <div class="arrow-btn" style="left:408px"><svg width="43" height="41" viewBox="0 0 43 41"><polyline points="25,12 17,20.5 25,29" fill="none" stroke="#fff" stroke-width="3"/></svg></div>
  <div class="arrow-btn" style="left:459px"><svg width="43" height="41" viewBox="0 0 43 41"><polyline points="18,12 26,20.5 18,29" fill="none" stroke="#fff" stroke-width="3"/></svg></div>
</div>

<div class="abs video" role="img" aria-label="Video still of a man in a light blue button shirt leaning on a wall">
  <svg class="abs play" width="54" height="54" viewBox="0 0 54 54"><circle cx="27" cy="27" r="26" fill="rgba(255,255,255,.85)"/><polygon points="21,16 39,27 21,38" fill="#2d2927"/></svg>
</div>

<section class="abs features">
  <div class="abs feature" style="left:96px">
    <div class="bar heading"><svg width="34" height="30" viewBox="0 0 34 30"><rect x="2" y="5" width="30" height="20" rx="2" fill="none" stroke="#fff" stroke-width="2.5"/><rect x="2" y="10" width="30" height="4" fill="#fff"/></svg>Payment Method</div>
    <div class="rule"></div>
    <p class="text">Lorem ipsum dolor sit amet. omnis aperiam ab ipsam ipsa odit</p>
    <div class="cards"><span></span><span></span><span></span><span></span></div>
    <div class="btn read-more">Read More</div>
  </div>
  <div class="abs feature mid" style="left:431px">
    <div class="bar heading"><svg width="40" height="28" viewBox="0 0 40 28"><rect x="1" y="3" width="24" height="17" fill="#fff"/><polygon points="26,8 34,8 39,14 39,20 26,20" fill="#fff"/><circle cx="9" cy="23" r="4" fill="#fff"/><circle cx="31" cy="23" r="4" fill="#fff"/></svg>Free Shipping</div>
    <div class="rule"></div>
    <p class="text">Lorem ipsum dolor sit amet. omnis aperiam ab ipsam ipsa odit aut aperiam aspernatur ventatis unde enim accusantium laudantium</p>
    <div class="btn read-more">Read More</div>
  </div>
  <div class="abs feature" style="left:769px">
    <div class="bar heading"><svg width="26" height="32" viewBox="0 0 26 32"><path d="M6 14 V9 a7 7 0 0 1 14 0 V14" fill="none" stroke="#fff" stroke-width="3"/><rect x="2" y="14" width="22" height="17" rx="2" fill="#fff"/></svg>Secure Shopping</div>
    <div class="rule"></div>
    <p class="text">Lorem ipsum dolor sit amet. omnis aperiam ab ipsam ipsa odit aut aperiam aspernatur ventatis unde enim accusantium laudantium</p>
    <div class="btn read-more">Read More</div>
  </div>
</section>

<footer class="abs footer">
  <div class="abs copy">© 2014 <b>YOUR COMPANY</b>. ALL RIGHTS RESERVED.</div>
  <div class="abs fnav"><span>About us</span><span>Term and use</span><span>Privacy policy</span><span>FAQs</span><span>Contact us</span></div>
  <div class="abs social"><span style="background:#3b5a98"></span><span style="background:#2aa9e0"></span><span style="background:#d8322a"></span><span style="background:#1d7fb4"></span><span style="background:#c9232a"></span></div>
</footer>

</body>
</html>
```